Verdant Systems Business Card

want the back of card to be blue- with the logo in the center
front of card- info plus logo (info being mailing address, email address, and website address )
4 different names with titles to have on cards
1) Calvin Borsted - Owner
2) Naomi Trelvik- Customer Relationship Specialist
3) Felix Andrade- Vice President of Sales
4) Owen Markby- Chief Technology Officer

Target Market(s)

tech company in the government/probation office industry

Industry/Entity Type

Government Office

Contact Information for Business Card

1) Calvin Borsted - Owner

Colors
0355a3
ffffff

Requirements
Must have
• back side should be blue, with the logo placed in the center
• front side needs to include both the logo, as well as company info (info should include website address, email address, and mailing address)

```html
<!DOCTYPE html>
<html lang="en">
<head>
<meta charset="utf-8">
<title>Verdant Systems Business Card</title>
<link rel="stylesheet" href="https://fonts.googleapis.com/css2?family=PT+Serif&family=Roboto:wght@400&display=swap">
<style>
  :root {
    --backdrop: #b4b2b3;
    --paper: #fbfbfb;
    --brand-blue: #0355a3;
    --navy: #253766;
    --slate: #8e8e96;
    --ink-grey: #6f6f76;
    --pale: #ececef;
    --white: #ffffff;
  }
  * { margin: 0; padding: 0; box-sizing: border-box; }
  html, body { width: 1200px; height: 1200px; overflow: hidden; }
  body { background: var(--backdrop); position: relative; font-family: "Roboto", Arial, sans-serif; }

  .card {
    position: absolute;
    border-radius: 22px;
    overflow: hidden;
  }

  .wordmark {
    font-family: "PT Serif", Georgia, serif;
    font-weight: 400;
    letter-spacing: 2px;
    text-transform: uppercase;
    white-space: nowrap;
  }
  .brand-dot { border-radius: 50%; }

  /* Back side: brand blue with centred name */
  .card-back {
    left: 238px; top: 120px; width: 712px; height: 417px;
    background: var(--brand-blue);
  }
  .card-back .brand {
    position: absolute; left: 0; right: 0; top: 172px;
    display: flex; align-items: center; justify-content: center; gap: 18px;
  }
  .card-back .brand-dot { width: 22px; height: 22px; background: var(--white); }
  .card-back .wordmark { font-size: 50px; color: var(--white); line-height: 60px; }
  .site-line {
    position: absolute; left: 0; right: 0; top: 372px;
    display: flex; align-items: center; justify-content: center; gap: 22px;
    color: var(--white); font-size: 16px;
  }
  .site-line .dash { width: 46px; height: 3px; background: var(--white); border-radius: 2px; }
  .band { position: absolute; bottom: 0; height: 14px; }
  .band-navy { left: 0; width: 356px; background: var(--navy); }
  .band-slate { left: 356px; right: 0; background: var(--slate); }

  /* Front side */
  .card-front { left: 230px; top: 645px; width: 720px; height: 415px; background: var(--paper); }
  .decor-circle {
    position: absolute; left: -150px; top: 30px;
    width: 420px; height: 420px; border-radius: 50%;
    background: var(--pale);
  }
  .card-front .brand {
    position: absolute; right: 36px; top: 44px;
    display: flex; align-items: center; gap: 12px;
  }
  .card-front .brand-dot { width: 14px; height: 14px; background: var(--navy); }
  .card-front .wordmark { font-size: 34px; color: var(--navy); }
  .tab {
    position: absolute; right: 0; top: 180px;
    width: 18px; height: 72px;
    background: var(--navy);
    border-radius: 36px 0 0 36px;
  }
  .person { position: absolute; right: 36px; top: 188px; text-align: right; }
  .person-name { font-family: "PT Serif", Georgia, serif; font-size: 25px; color: var(--navy); letter-spacing: 1px; text-transform: uppercase; }
  .person-title { font-size: 16px; color: var(--ink-grey); margin-top: 6px; }
  .contact { position: absolute; right: 30px; top: 283px; list-style: none; text-align: right; }
  .contact li {
    display: flex; justify-content: flex-end; align-items: center; gap: 14px;
    font-size: 16.5px; color: var(--ink-grey); height: 26px;
  }
  .contact svg { width: 16px; height: 16px; fill: var(--navy); }
  .address { position: absolute; right: 34px; top: 367px; font-size: 16.5px; color: var(--ink-grey); }
</style>
</head>
<body>

<section class="card card-back" aria-label="Card back">
  <div class="brand">
    <span class="brand-dot"></span>
    <span class="wordmark">Verdant Systems</span>
  </div>
  <div class="site-line">
    <span class="dash"></span>
    <span>www.HallbrookCapital.com</span>
    <span class="dash"></span>
  </div>
  <div class="band band-navy"></div>
  <div class="band band-slate"></div>
</section>

<section class="card card-front" aria-label="Card front">
  <div class="decor-circle"></div>
  <div class="brand">
    <span class="brand-dot"></span>
    <span class="wordmark">Verdant Systems</span>
  </div>
  <div class="tab"></div>
  <div class="person">
    <div class="person-name">Naomi Trelvik</div>
    <div class="person-title">Customer Relationship Specialist</div>
  </div>
  <ul class="contact">
    <li>111-111-1111
      <svg viewBox="0 0 16 16" aria-hidden="true"><path d="M2 5c0-2 2-3 6-3s6 1 6 3v1h-3V5H5v1H2zM4 7h8l2 6H2z"/></svg>
    </li>
    <li>naomi.t@verdantsystems.com
      <svg viewBox="0 0 16 16" aria-hidden="true"><path d="M1 3h14v10H1zM2.5 4.5 8 9l5.5-4.5V4H2.5z" fill-rule="evenodd"/></svg>
    </li>
    <li>www.verdantsystems.com
      <svg viewBox="0 0 16 16" aria-hidden="true"><path d="M8 1a7 7 0 1 0 0 14A7 7 0 0 0 8 1zm0 1.5c.8 0 1.7 1.6 2 4H6c.3-2.4 1.2-4 2-4zM2.6 7h2.4a12 12 0 0 0 0 2H2.6a5.5 5.5 0 0 1 0-2zm3.4 0h4a11 11 0 0 1 0 2H6a11 11 0 0 1 0-2zm5 0h2.4a5.5 5.5 0 0 1 0 2H11a12 12 0 0 0 0-2zM6 9.5h4c-.3 2.4-1.2 4-2 4s-1.7-1.6-2-4z"/></svg>
    </li>
  </ul>
  <div class="address">234 Anywhere St., Any City, Town, US 123456</div>
</section>

</body>
</html>
```